Process Serving Company needs a letterhead design

Looking to have a letterhead designed for letters to attorneys advertising our business. We would like something eye catching but professional. Colors and logos are attached. Please add "Process Service and Attorney Support" near the logo or header

Target Market(s)

Attorneys

Font styles to use
Serif
Sans Serif

Colors
33a6d7
0255a3
85cae6
cee9f5
ecf7fb

```html
<!DOCTYPE html>
<html lang="en">
<head>
<meta charset="utf-8">
<title>Saguaro Swift Serve Letterhead</title>
<link rel="stylesheet" href="https://fonts.googleapis.com/css2?family=Source+Sans+3:wght@400;600&family=Arimo:wght@700&display=swap">
<style>
  :root {
    --brand-blue: #33a6d7;
    --brand-navy: #0255a3;
    --brand-sky: #85cae6;
    --ink: #4a4a4a;
    --ink-dark: #3a3a3a;
    --paper: #f9f9f9;
    --backdrop: #e4e4e4;
    --white: #ffffff;
  }
  * { margin: 0; padding: 0; box-sizing: border-box; }
  html, body {
    width: 1059px; height: 1200px; overflow: hidden;
    background: var(--backdrop);
  }
  .letterhead {
    position: absolute; left: 125px; top: 30px;
    width: 808px; height: 1140px;
    background: var(--paper);
    font-family: "Source Sans 3", sans-serif;
    color: var(--ink);
  }
  .brand {
    position: absolute; top: 58px; left: 0; right: 0;
    display: flex; justify-content: center; align-items: center; gap: 10px;
  }
  .brand-mark {
    width: 14px; height: 14px; background: var(--brand-blue);
  }
  .brand-name {
    font-family: "Source Sans 3", sans-serif;
    font-weight: 400; font-size: 30px; letter-spacing: 0.5px;
    color: var(--brand-blue); text-transform: uppercase;
  }
  .letter-body {
    position: absolute; top: 260px; left: 61px; width: 686px;
  }
  .salutation {
    font-family: "Arimo", sans-serif; font-weight: 700;
    font-size: 18px; line-height: 22px; color: var(--ink-dark); margin-bottom: 25px;
  }
  .letter-body p {
    font-size: 17px; line-height: 21px; text-align: justify;
    letter-spacing: -0.1px;
    margin-bottom: 21px;
  }
  .signature {
    position: absolute; top: 876px; left: 61px;
    width: 153px; height: 74px;
    background: linear-gradient(90deg, #e9e9e9, #dcdcdc);
    border-radius: 4px;
  }
  .contact-band {
    position: absolute; left: 0; bottom: 0; width: 808px; height: 30px;
  }
  .contact-band svg { position: absolute; inset: 0; }
  .contact-list {
    position: absolute; left: 66px; top: 0; height: 30px;
    display: flex; align-items: center; gap: 7px;
    font-size: 11px; color: var(--white);
  }
  .contact-item { display: flex; align-items: center; gap: 3px; }
  .contact-item svg { position: static; }
  .web-address {
    position: absolute; left: 573px; width: 185px; top: 0; height: 30px;
    display: flex; align-items: center; justify-content: center;
    font-size: 13px; letter-spacing: 0.6px; color: var(--white);
  }
</style>
</head>
<body>
  <div class="letterhead">
    <header class="brand">
      <span class="brand-mark"></span>
      <span class="brand-name">Saguaro Swift Serve</span>
    </header>

    <main class="letter-body">
      <h1 class="salutation">Dear Mr. John,</h1>
      <p>Lorem Ipsum is simply dummy text of the printing and typesetting industry. Lorem Ipsum has been the industry's standard dummy text ever since the 1500s, when an unknown printer took a galley of type and scrambled it to make a type specimen book. It has survived not only five centuries, but also the leap into electronic typesetting, remaining essentially unchanged.</p>
      <p>The standard chunk of Lorem Ipsum used since the 1500s is reproduced below for those interested. Sections 1.10.32 and 1.10.33 from "de Finibus Bonorum et Malorum" by Tullian Maro are also reproduced in their exact original form, accompanied by English versions from the 1914 translation by E. Tamsworth</p>
      <p>Lorem Ipsum is simply dummy text of the printing and typesetting industry. Lorem Ipsum has been the industry's standard dummy text ever since the 1500s, when an unknown printer took a galley of type and scrambled it to make a type specimen book. It has survived not only five centuries, but also the leap into electronic typesetting, remaining essentially unchanged. It was popularised in the</p>
      <p>Lorem Ipsum is simply dummy text of the printing and typesetting industry. Lorem Ipsum has been the industry's standard dummy text ever since the 1500s, when an unknown printer took a galley of type and scrambled it to make a type specimen book. It has survived not only five centuries, but also the leap into electronic typesetting, remaining essentially unchanged. It was popularised in the</p>
      <p>Lorem Ipsum is simply dummy text of the printing and typesetting industry. Lorem Ipsum has been the industry's standard dummy text ever since the 1500s, when an unknown printer took a galley of type and scrambled it to make a type specimen book.</p>
    </main>

    <div class="signature" role="img" aria-label="Handwritten signature of the sender"></div>

    <footer class="contact-band">
      <svg width="808" height="30" viewBox="0 0 808 30">
        <rect x="0" y="0" width="808" height="30" fill="var(--brand-blue)"/>
        <polygon points="568,0 758,0 768,15 758,30 568,30 578,15" fill="var(--brand-navy)"/>
        <polyline points="569,0 579,15 569,30" fill="none" stroke="var(--white)" stroke-width="2"/>
        <polyline points="759,0 769,15 759,30" fill="none" stroke="var(--white)" stroke-width="2"/>
      </svg>
      <div class="contact-list">
        <span class="contact-item">
          <svg width="9" height="9" viewBox="0 0 10 10"><path d="M2 1 L4 3 L3 4.5 Q4.5 6.5 5.5 7 L7 6 L9 8 L7.5 9.5 Q3 8.5 0.5 2.5 Z" fill="var(--white)"/></svg>
          480-555-0142
        </span>
        <span class="contact-item">
          <svg width="9" height="9" viewBox="0 0 10 10"><rect x="2.5" y="0.5" width="5" height="3" fill="var(--white)"/><rect x="0.5" y="3.5" width="9" height="4" rx="1" fill="var(--white)"/><rect x="2.5" y="6.5" width="5" height="3" fill="var(--white)"/></svg>
          480-555-0142
        </span>
        <span class="contact-item">
          <svg width="11" height="8" viewBox="0 0 11 8"><rect x="0.5" y="0.5" width="10" height="7" fill="none" stroke="var(--white)"/><polyline points="0.5,0.5 5.5,4.5 10.5,0.5" fill="none" stroke="var(--white)"/></svg>
          info@SwiftServeDocs.com
        </span>
      </div>
      <div class="web-address">www.SwiftServeDocs.com</div>
    </footer>
  </div>
</body>
</html>
```